Clendora Hand Sanitizer One Page Website

I need someone to make a one page website for us. The site is www.clendora-example.com. I quickly created a simple basic page with all the elements (text, picture, table of pricing, pdf links) needed. I need someone to make the webpage look nice, professioonal, and responsive. There are only 2 links on the page pointing to two pdf files, otherwise there is no navigation needed. The product is a hand sanitizer.
Target Market(s)
Government, corporations, hospitals, large companies
Number of Pages Required
1 page
Requirements
Nice to have
- A hero image relating to hand sanitizer products would be really nice
We would like the bulleted items (Active Ingredient 75% Isopropyl Alcohol, etc) to somehow incorporate icons like the attached picture.

```html
<!DOCTYPE html>
<html lang="en">
<head>
<meta charset="utf-8">
<title>Clendora Hand Sanitizer</title>
<link href="https://fonts.googleapis.com/css2?family=Poppins:wght@600;700&family=Inter:wght@400;500;600&family=Oswald:wght@700&display=swap" rel="stylesheet">
<style>
:root{
  --navy:#0b1a7c;
  --ink:#333333;
  --teal-dark:#17495e;
  --green:#228b3e;
  --slate:#24263a;
  --teal:#17806f;
  --brand-green:#1fc24a;
  --brand-blue:#1a8ac4;
  --gray-band:#eeeeee;
  --row:#e3e3e3;
  --yellow:#fdc40d;
  --white:#ffffff;
}
*{margin:0;padding:0;box-sizing:border-box}
html,body{width:1019px;height:1200px;overflow:hidden;background:var(--white);font-family:'Inter',sans-serif;color:var(--ink)}
.page{position:relative;width:1019px;height:1200px}
.hero{position:absolute;left:0;top:0;width:1019px;height:415px;
  background:radial-gradient(ellipse at 60% 70%,#cfcfcf 0%,#a9a9a9 35%,#f2f2f2 75%,#ffffff 100%)}
.site-header{position:absolute;left:80px;top:22px;right:81px;display:flex;justify-content:space-between;align-items:flex-start}
.brand{display:flex;flex-direction:column}
.brand-row{display:flex;align-items:center;gap:8px}
.brand-dot{width:26px;height:26px;border-radius:50%;background:var(--brand-blue)}
.brand-name{font-family:'Inter',sans-serif;font-weight:600;font-size:30px;color:#3a3a3a;letter-spacing:.5px;line-height:34px}
.brand-sub{font-family:'Inter',sans-serif;font-weight:600;font-size:14px;color:var(--brand-green);letter-spacing:.5px;margin-top:2px}
.doc-links{display:flex;gap:22px;font-size:12px;font-weight:500;margin-top:14px}
.doc-links a{text-decoration:none}
.doc-links .compliance{color:var(--navy)}
.doc-links .sep{color:#333}
.doc-links .sds{color:#333}
.cta{position:absolute;left:380px;top:189px;width:259px;height:38px;background:var(--navy);color:var(--white);
  font-size:13px;font-weight:600;display:flex;align-items:center;justify-content:center;gap:12px;text-decoration:none}
.features{position:absolute;left:0;top:415px;width:1019px;height:449px;background:var(--gray-band)}
.features-bg{position:absolute;left:100px;top:90px;width:790px;height:359px;
  background:linear-gradient(180deg,rgba(255,255,255,0) 0%,rgba(255,255,255,.45) 60%,rgba(255,255,255,.25) 100%)}
.headline{position:absolute;left:0;top:49px;width:1019px;text-align:center;font-family:'Poppins',sans-serif;font-weight:700;font-size:25px;line-height:31px;color:var(--ink)}
.headline em{font-style:normal;color:var(--navy)}
.badge{position:absolute;top:150px;width:160px;text-align:center}
.badge svg{display:block;margin:0 auto}
.badge-label{font-size:14px;font-weight:600;line-height:18px;margin-top:14px}
.hex-text{font-family:'Oswald',sans-serif;font-weight:700}
.fda{position:absolute;left:0;top:403px;width:1019px;text-align:center;font-size:14px;color:#111}
.stock{position:absolute;left:80px;top:901px;width:188px;height:33px;background:var(--yellow);color:#222;
  font-size:14px;font-weight:600;display:flex;align-items:center;justify-content:center}
.pricing{position:absolute;left:80px;top:953px;width:858px;border-collapse:separate;border-spacing:2px 2px;margin-left:-2px}
.pricing th{background:var(--navy);color:var(--white);font-weight:600;font-size:14px;text-align:left;padding:0 12px;height:32px}
.pricing td{background:var(--row);font-size:14px;color:#222;padding:0 12px;height:30px}
.footer{position:absolute;left:0;top:1145px;width:1019px;height:55px;background:var(--navy);color:var(--white);
  display:flex;align-items:center;justify-content:center;font-size:15px;font-weight:600}
</style>
</head>
<body>
<div class="page">
  <div class="hero" role="img" aria-label="Black and white photo of a hand pressing a pump bottle, dispensing sanitizer gel into an open palm"></div>

  <header class="site-header">
    <div class="brand">
      <div class="brand-row"><span class="brand-dot"></span><span class="brand-name">Brightwell</span></div>
      <span class="brand-sub">CLENDORA</span>
    </div>
    <nav class="doc-links">
      <a class="compliance" href="#">Letter of Compliance</a>
      <span class="sep">|</span>
      <a class="sds" href="#">Safety Data Sheet</a>
    </nav>
  </header>

  <a class="cta" href="#">Enquire Now on 555-210-3380
    <svg width="16" height="10" viewBox="0 0 16 10"><path d="M0 5h14M10 1l4 4-4 4" fill="none" stroke="#fff" stroke-width="1.5"/></svg>
  </a>

  <section class="features">
    <div class="features-bg" role="img" aria-label="Faded photo of gallon sanitizer jugs"></div>
    <h1 class="headline">Isopropyl Alcohol Antiseptic <em>75% Topical Solution</em><br>Hand Sanitizer</h1>

    <div class="badge" style="left:85px">
      <svg width="140" height="160" viewBox="0 0 140 160"><polygon points="70,4 134,41 134,119 70,156 6,119 6,41" fill="none" stroke="var(--teal-dark)" stroke-width="5"/>
        <text class="hex-text" x="70" y="97" text-anchor="middle" font-size="48" fill="var(--teal-dark)">75%</text></svg>
      <p class="badge-label" style="color:var(--teal-dark)">Active Ingredient<br>Isopropyl Alcohol</p>
    </div>

    <div class="badge" style="left:256px">
      <svg width="140" height="160" viewBox="0 0 140 160"><polygon points="70,4 134,41 134,119 70,156 6,119 6,41" fill="none" stroke="var(--navy)" stroke-width="5"/>
        <text class="hex-text" x="70" y="97" text-anchor="middle" font-size="44" fill="var(--navy)">CFSA</text></svg>
      <p class="badge-label" style="color:var(--navy)">Rated E3<br>Hand Sanitizer</p>
    </div>

    <div class="badge" style="left:427px">
      <svg width="140" height="160" viewBox="0 0 140 160"><polygon points="70,4 134,41 134,119 70,156 6,119 6,41" fill="none" stroke="var(--green)" stroke-width="5"/>
        <text class="hex-text" x="70" y="97" text-anchor="middle" font-size="48" fill="var(--green)">GHO</text></svg>
      <p class="badge-label" style="color:var(--green)">Guidelines<br>Recognized</p>
    </div>

    <div class="badge" style="left:599px">
      <svg width="140" height="160" viewBox="0 0 140 160"><polygon points="70,4 134,41 134,119 70,156 6,119 6,41" fill="none" stroke="var(--slate)" stroke-width="5"/>
        <text class="hex-text" x="70" y="70" text-anchor="middle" font-size="26" fill="var(--slate)">1,5,55</text>
        <text class="hex-text" x="70" y="113" text-anchor="middle" font-size="46" fill="var(--slate)">275</text></svg>
      <p class="badge-label" style="color:var(--slate)">Gallon Packages<br>Available</p>
    </div>

    <div class="badge" style="left:770px">
      <svg width="140" height="160" viewBox="0 0 140 160"><polygon points="70,4 134,41 134,119 70,156 6,119 6,41" fill="none" stroke="var(--teal)" stroke-width="5"/>
        <text class="hex-text" x="70" y="72" text-anchor="middle" font-size="32" fill="var(--teal)">EFFEC</text>
        <text class="hex-text" x="70" y="111" text-anchor="middle" font-size="40" fill="var(--teal)">TIVE</text></svg>
      <p class="badge-label" style="color:var(--teal);margin-top:6px">Killing Germs<br>without drying<br>out your hands</p>
    </div>

    <p class="fda">FDA drug registration number (61234-507)</p>
  </section>

  <div class="stock">In Stock Ready to Ship</div>

  <table class="pricing">
    <colgroup><col style="width:185px"><col style="width:145px"><col style="width:186px"><col style="width:143px"><col style="width:195px"></colgroup>
    <thead><tr><th>Container</th><th>Min Order Qty</th><th>Price ($ Per Gallon)</th><th>Part Number</th><th>Price Per Ounce</th></tr></thead>
    <tbody>
      <tr><td>1 Gallon / 4 per case</td><td>48</td><td>$27.92</td><td>IP4148</td><td>0.218125</td></tr>
      <tr><td>5 Gallon Pail</td><td>36</td><td>$25.86</td><td>IP5400</td><td>0.202031</td></tr>
      <tr><td>55 Gallon Drum</td><td>4</td><td>$22.42</td><td>IP5540</td><td>0.175156</td></tr>
      <tr><td>275 Gallon Tote</td><td>1</td><td>$20.24</td><td>IP2751</td><td>0.158125</td></tr>
    </tbody>
  </table>

  <footer class="footer">Call 555-210-3380 for inquiries</footer>
</div>
</body>
</html>
```